Marlowe Dance Academy- Stationery
Stationery-biz card/letterhead/envelope/postcard
Creative Brief
Use same font as used in my logo
Dana Volpitch
Owner/Artistic Director
Fernhill Plaza 7412 Fernhill Drive Westbrook, OH 44987
info@mdadance.com
www.mdadance.com
Tagline: Discovering Dance...Inspiring Dreams...Creating Artists
Looking for creativity from designer

```html
<!DOCTYPE html>
<html lang="en">
<head>
<meta charset="utf-8">
<title>Marlowe Dance Academy – Stationery</title>
<link href="https://fonts.googleapis.com/css2?family=Cormorant+Garamond:wght@500;600&display=swap" rel="stylesheet">
<style>
  :root{
    --stage:#3b3c3e;
    --teal:#2bb0b8;
    --teal-deep:#1f5257;
    --paper:#ffffff;
    --ink:#2d5a5e;
    --muted:#7f9a9c;
  }
  *{margin:0;padding:0;box-sizing:border-box}
  html,body{width:1200px;height:271px;overflow:hidden;background:var(--stage)}
  body{position:relative;font-family:"Cormorant Garamond",Georgia,serif;color:var(--ink)}
  .piece{position:absolute;overflow:hidden;box-shadow:0 2px 5px rgba(0,0,0,.45)}
  .piece svg{position:absolute;inset:0;width:100%;height:100%}
  .wordmark{position:absolute;font-weight:600;text-align:center;line-height:1.05;white-space:nowrap}
  .small{position:absolute;font-size:4.2px;line-height:1.35;white-space:nowrap}

  .stage-mark{position:absolute;left:150px;top:20px;width:110px;color:var(--paper);font-size:15px;text-align:center;font-weight:600;line-height:1.1}
  .stage-mark span{display:block;font-size:7px;font-weight:500;letter-spacing:.5px;margin-top:3px;color:#cfe3e4}

  .card-tall{width:56px;height:108px;top:42px;background:var(--teal-deep)}
  .card-tall .wordmark{left:0;right:0;top:22px;color:var(--paper);font-size:7px}
  .card-wide{width:100px;height:58px;top:172px}
  .card-wide.white{background:var(--paper)}
  .card-wide.teal{background:var(--teal)}
  .card-wide .wordmark{left:0;right:0;top:16px;font-size:7px}

  .card-contact{left:264px;top:52px;width:76px;height:48px;background:var(--paper)}

  .letterhead{width:122px;height:230px;top:20px;background:var(--paper)}
  .letterhead .wordmark{left:0;right:0;top:12px;font-size:6px;color:var(--ink)}

  .envelope-dl{left:656px;width:172px;height:70px;background:var(--paper)}
</style>
</head>
<body>

  <div class="stage-mark">Marlowe Dance Academy<span>Discovering Dance...Inspiring Dreams</span></div>

  <!-- vertical business cards -->
  <div class="piece card-tall" style="left:24px">
    <svg viewBox="0 0 56 108" preserveAspectRatio="none"><path d="M0 70 Q28 58 56 76 V108 H0Z" fill="var(--paper)"/><path d="M0 70 Q28 58 56 76" stroke="var(--teal)" stroke-width="2" fill="none"/></svg>
    <div class="wordmark">Marlowe<br>Dance<br>Academy</div>
  </div>
  <div class="piece card-tall" style="left:88px;background:var(--teal)">
    <svg viewBox="0 0 56 108" preserveAspectRatio="none"><path d="M0 64 Q30 52 56 70 V108 H0Z" fill="var(--paper)"/></svg>
    <div class="wordmark">Marlowe<br>Dance<br>Academy</div>
    <div class="small" style="left:6px;top:80px;color:var(--ink)">Dana Volpitch<br>www.mdadance.com</div>
  </div>

  <!-- contact card -->
  <div class="piece card-contact">
    <svg viewBox="0 0 76 48" preserveAspectRatio="none"><path d="M0 40 Q38 30 76 42 V48 H0Z" fill="var(--teal)"/></svg>
    <div class="small" style="left:5px;top:5px;font-size:5px;font-weight:600">Dana Volpitch</div>
    <div class="small" style="left:5px;top:12px;color:var(--muted)">Owner/Artistic Director<br>Fernhill Plaza<br>7412 Fernhill Drive<br>Westbrook, OH 44987<br>info@mdadance.com</div>
  </div>

  <!-- horizontal cards -->
  <div class="piece card-wide white" style="left:24px">
    <svg viewBox="0 0 100 58" preserveAspectRatio="none"><path d="M0 46 Q50 34 100 48 V58 H0Z" fill="var(--teal)"/></svg>
    <div class="wordmark" style="color:var(--ink)">Marlowe Dance Academy</div>
  </div>
  <div class="piece card-wide white" style="left:132px">
    <svg viewBox="0 0 100 58" preserveAspectRatio="none"><path d="M60 0 Q74 30 100 36 V0Z" fill="var(--teal)"/></svg>
    <div class="small" style="left:6px;top:8px;font-size:5px;font-weight:600">Dana Volpitch</div>
    <div class="small" style="left:6px;top:15px;color:var(--muted)">Fernhill Plaza<br>7412 Fernhill Drive<br>Westbrook, OH 44987<br>www.mdadance.com</div>
  </div>
  <div class="piece card-wide teal" style="left:240px">
    <svg viewBox="0 0 100 58" preserveAspectRatio="none"><path d="M0 44 Q50 32 100 46" stroke="var(--paper)" stroke-width="1.5" fill="none"/></svg>
    <div class="wordmark" style="color:var(--paper)">Marlowe Dance Academy</div>
  </div>

  <!-- letterheads -->
  <div class="piece letterhead" style="left:362px">
    <svg viewBox="0 0 122 230" preserveAspectRatio="none"><path d="M0 214 Q60 198 122 216 V230 H0Z" fill="var(--teal)"/></svg>
    <div class="wordmark">Marlowe Dance Academy</div>
  </div>
  <div class="piece letterhead" style="left:504px">
    <svg viewBox="0 0 122 230" preserveAspectRatio="none"><path d="M0 0 H122 V10 Q60 20 0 6Z" fill="var(--teal)"/><path d="M0 220 Q60 208 122 224 V230 H0Z" fill="var(--teal)"/></svg>
    <div class="wordmark" style="top:22px">Marlowe Dance Academy</div>
  </div>

  <!-- small envelopes -->
  <div class="piece envelope-dl" style="top:52px">
    <svg viewBox="0 0 172 70" preserveAspectRatio="none"><path d="M0 58 Q86 46 172 60 V70 H0Z" fill="var(--teal)"/></svg>
    <div class="wordmark" style="left:8px;top:8px;font-size:6px;text-align:left">Marlowe Dance Academy</div>
    <div class="small" style="left:8px;top:16px;color:var(--muted)">7412 Fernhill Drive<br>Westbrook, OH 44987</div>
  </div>
  <div class="piece envelope-dl" style="top:152px">
    <svg viewBox="0 0 172 70" preserveAspectRatio="none"><path d="M0 0 L86 34 L172 0" stroke="#dfe7e8" stroke-width="1" fill="none"/><path d="M0 60 Q86 50 172 62 V70 H0Z" fill="var(--teal)"/></svg>
  </div>

  <!-- large envelopes -->
  <div class="piece" style="left:866px;top:52px;width:300px;height:80px;background:var(--teal)">
    <svg viewBox="0 0 300 80" preserveAspectRatio="none"><path d="M0 0 L150 44 L300 0Z" fill="var(--teal-deep)"/><path d="M0 80 L150 40 L300 80" stroke="#ffffff55" stroke-width="1" fill="none"/></svg>
  </div>
  <div class="piece" style="left:866px;top:144px;width:300px;height:84px;background:var(--paper)">
    <svg viewBox="0 0 300 84" preserveAspectRatio="none"><path d="M0 70 Q150 54 300 72 V84 H0Z" fill="var(--teal)"/></svg>
    <div class="wordmark" style="left:12px;top:10px;font-size:8px;text-align:left">Marlowe Dance Academy</div>
    <div class="small" style="left:12px;top:21px;font-size:5px;color:var(--muted)">Fernhill Plaza · 7412 Fernhill Drive<br>Westbrook, OH 44987</div>
  </div>

</body>
</html>
```